Advertisement Design Project

I would like to have some advertisement ideas to promote my business. Our company provides credit repair, tax preparation, notary service, ledger preparation (for small businesses and independent contractors) tax restoration (help people with liens, levy, garnishments, etc. by negotiating with the NTB in these matters)

The name of our company is Vel Marin Financing
Our "BrivoMendup" program focuses on tax preparation, restoration, and credit repair.
Our "Brisk Start" program prepares ledgers for small business and independent contractors by preparing monthly ledgers so that at tax season they are not having to look everywhere for their receipts in order to get all deductions due to them during the tax season.

We need something that is catchy and will gain attention

attached is our logo. Our slogan is "Happiness, Restored!"

Thank you!

Target Market(s)

The financially distressed
Small business owners
Independent contractors
businesses that rely on credit worthy clients to do business with

Industry/Entity Type

Small Business

Requirements
Must have
• great pictures
nice layout

```html
<!DOCTYPE html>
<html lang="en">
<head>
<meta charset="utf-8">
<title>Vel Marin Financing – Flyer</title>
<link rel="stylesheet" href="https://fonts.googleapis.com/css2?family=Source+Sans+3:wght@400;600&display=swap">
<style>
  :root {
    --page-bg: #d9dadc;
    --flyer-bg: #f5f8fa;
    --ink: #111418;
    --title-blue: #6cc4e4;
    --white: #ffffff;
    --navy: #1b3a63;
    --swoosh-blue: #1f6fb8;
    --swoosh-light: #8fd3ec;
  }
  * { margin: 0; padding: 0; box-sizing: border-box; }
  html, body { width: 1200px; height: 844px; overflow: hidden; background: var(--page-bg); }
  body { font-family: "Source Sans 3", "Myriad Pro", Arial, sans-serif; color: var(--ink); }

  .flyer {
    position: absolute; left: 50px; top: 10px;
    width: 1100px; height: 824px;
    background: var(--flyer-bg);
    overflow: hidden;
  }
  .swoosh { position: absolute; left: 0; top: 0; width: 1100px; height: 824px; }
  .swoosh-bottom { z-index: 2; }

  .brand-title {
    position: absolute; left: 36px; top: 22px;
    font-size: 50px; font-weight: 400; color: var(--title-blue);
    line-height: 1.1; white-space: nowrap;
  }
  .slogan {
    position: absolute; left: 90px; top: 96px;
    font-size: 27px; color: var(--white); white-space: nowrap;
  }
  .brand-mark {
    position: absolute; left: 903px; top: 24px;
    width: 170px; height: 175px;
    background: var(--navy);
    border: 6px solid var(--white);
    display: flex; align-items: flex-end; justify-content: center;
    text-align: center; padding: 0 8px 26px;
    font-size: 17px; color: var(--white); line-height: 1.2;
  }

  .services { position: absolute; left: 29px; top: 218px; }
  .services h2 { font-size: 45px; font-weight: 400; line-height: 1.1; margin-bottom: 4px; white-space: nowrap; }
  .services ul { list-style: none; font-size: 26px; line-height: 34.5px; white-space: nowrap; }

  .program { position: absolute; left: 431px; top: 256px; }
  .program h3 { font-size: 31px; font-weight: 400; line-height: 1.2; margin-bottom: 0; white-space: nowrap; }
  .program ul { list-style: none; font-size: 26px; line-height: 34.5px; padding-left: 19px; white-space: nowrap; }

  .photo { position: absolute; border: 6px solid var(--white); z-index: 1; }
  .photo-money {
    left: 785px; top: 279px; width: 284px; height: 187px;
    background:
      radial-gradient(ellipse at 70% 20%, #c9cbcd 0%, transparent 45%),
      radial-gradient(ellipse at 55% 75%, #efe6b4 0%, transparent 40%),
      linear-gradient(135deg, #a9b595 0%, #d8dcc4 45%, #cfcfc9 70%, #8e9398 100%);
  }
  .photo-meeting {
    left: 440px; top: 410px; width: 391px; height: 272px;
    background:
      radial-gradient(ellipse at 80% 70%, #243249 0%, transparent 38%),
      radial-gradient(ellipse at 20% 70%, #1f2a3d 0%, transparent 30%),
      radial-gradient(ellipse at 50% 60%, #e4d9cc 0%, transparent 35%),
      linear-gradient(180deg, #f2f4f5 0%, #e2e5e7 45%, #b9bcc0 100%);
  }
  .photo-graphic {
    left: 831px; top: 471px; width: 237px; height: 152px;
    background:
      radial-gradient(ellipse at 65% 45%, #4fa7c2 0%, transparent 45%),
      radial-gradient(ellipse at 22% 65%, #2c8fc0 0%, transparent 22%),
      linear-gradient(135deg, #ffffff 0%, #e8f4f8 50%, #bfe0ea 100%);
  }
  .photo-office {
    left: 156px; top: 630px; width: 320px; height: 147px;
    background:
      radial-gradient(ellipse at 25% 40%, #3d4a57 0%, transparent 40%),
      radial-gradient(ellipse at 75% 45%, #e9d8c9 0%, transparent 30%),
      linear-gradient(135deg, #6d7a86 0%, #b4bcc3 50%, #eef0f2 100%);
  }

  .contact {
    position: absolute; left: 819px; top: 662px; z-index: 3;
    font-size: 28px; color: var(--white); letter-spacing: 0.5px;
  }
</style>
</head>
<body>
  <main class="flyer">
    <svg class="swoosh swoosh-top" viewBox="0 0 1100 824" aria-hidden="true">
      <defs>
        <linearGradient id="topBlack" x1="0" y1="0" x2="1" y2="0.3">
          <stop offset="0" stop-color="#0b0d10"/>
          <stop offset="0.5" stop-color="#34373b"/>
          <stop offset="1" stop-color="#050607"/>
        </linearGradient>
        <linearGradient id="topArc" x1="0" y1="1" x2="1" y2="0">
          <stop offset="0" stop-color="var(--swoosh-blue)"/>
          <stop offset="0.5" stop-color="var(--swoosh-light)"/>
          <stop offset="1" stop-color="#d8f0f8"/>
        </linearGradient>
      </defs>
      <path d="M0 0 H615 C500 118 270 196 0 200 Z" fill="url(#topArc)"/>
      <path d="M0 0 H560 C470 92 270 170 0 178 Z" fill="url(#topBlack)"/>
    </svg>

    <h1 class="brand-title">Vel Marin Financing</h1>
    <p class="slogan">Happiness, Restored!</p>
    <div class="brand-mark">Vel Marin Financing</div>

    <section class="services">
      <h2>Company provides</h2>
      <ul>
        <li>credit repair</li>
        <li>tax preparation</li>
        <li>notary service</li>
        <li>ledger preparation</li>
        <li>tax restoration (help people<br>with liens, levy, garnishments, etc.<br>by negotiating with the NTB in<br>these matters)</li>
      </ul>
    </section>

    <section class="program">
      <h3>"BrivoMendup" program</h3>
      <ul>
        <li>Tax preparation</li>
        <li>Restoration</li>
        <li>and credit repair.</li>
      </ul>
    </section>

    <div class="photo photo-money" role="img" aria-label="Photo of banknotes, a calculator and a 'Tax Time' note"></div>
    <div class="photo photo-meeting" role="img" aria-label="Photo of a couple shaking hands with a financial advisor"></div>
    <div class="photo photo-graphic" role="img" aria-label="Illustration of a figure pushing a puzzle-piece dollar sign"></div>
    <div class="photo photo-office" role="img" aria-label="Photo of a notary stamping a document beside a laptop"></div>

    <svg class="swoosh swoosh-bottom" viewBox="0 0 1100 824" aria-hidden="true">
      <defs>
        <linearGradient id="bottomArc" x1="0" y1="1" x2="1" y2="0">
          <stop offset="0" stop-color="var(--swoosh-blue)"/>
          <stop offset="0.55" stop-color="var(--swoosh-light)"/>
          <stop offset="1" stop-color="#d8f0f8"/>
        </linearGradient>
        <linearGradient id="bottomBlack" x1="0" y1="0" x2="1" y2="0">
          <stop offset="0" stop-color="#a3a7ab"/>
          <stop offset="0.4" stop-color="#1a1c1f"/>
          <stop offset="1" stop-color="#050607"/>
        </linearGradient>
      </defs>
      <path d="M367 824 C560 700 830 614 1100 608 V824 Z" fill="url(#bottomArc)"/>
      <path d="M462 824 C640 714 880 640 1100 636 V824 Z" fill="url(#bottomBlack)"/>
    </svg>

    <p class="contact">CONTACT</p>
  </main>
</body>
</html>
```